Business card for Eyelash extension salon in Cedar Vale,California USA

We need new business card for our salon in Cedar Vale. The salon name is 'Lashvera' . We would like to have...Business name: Lashvera Name of person: will provide later Address 4720 N.Alder Crest Ave Cedar Vale , CA 90477 Phone: will provide later (Text only) Web: www.lashverastudio.example Snapgrid icon, Circlebook icon follow us for seasonal campaign and news @lashverastudiolounge Design should look elegant, high-end, clean, simple, cohesive with my brand. Please refer my brand board. Business name color will be metallic bronzy color. Im thinking grey background or white background. Thanks

Target Market(s)

25-35. Gender neutral. People who are in Entertainment business industry.
This is High-end Eyelash extension salon in Cedar Vale

Industry/Entity Type

Beauty Salon

Contact Information for Business Card

Business name: Lashvera
Name of person: will provide later
Address 4720 N.Alder Crest Ave Cedar Vale , CA 90477
Phone: will provide later (Text only)
Web: www.lashverastudio.example
Snapgrid icon, Circlebook icon
follow us for seasonal campaign and news @lashverastudiolounge

Requirements
Must have
• Beautiful, elegant, clean and simple look but very attractive and modern
Should not have
• We don't like too clutter, too busy designs.

```html
<!DOCTYPE html>
<html lang="en">
<head>
<meta charset="utf-8">
<title>Lashvera Business Card</title>
<link href="https://fonts.googleapis.com/css2?family=Open+Sans:wght@400;600;700&display=swap" rel="stylesheet">
<style>
  :root {
    --backdrop: #2b2f36;
    --card: #1d1c1d;
    --bronze: #b48a68;
    --bronze-soft: #9c7658;
    --text-grey: #bdbab8;
    --text-dim: #8e8a87;
  }
  * { margin: 0; padding: 0; box-sizing: border-box; }
  html, body {
    width: 1200px; height: 1077px; overflow: hidden;
    background: var(--backdrop);
    font-family: "Open Sans", Arial, sans-serif;
  }
  .canvas { position: relative; width: 1200px; height: 1077px; }
  .card {
    position: absolute; width: 600px; height: 343px;
    border-radius: 26px; background: var(--card);
    box-shadow: 0 18px 40px rgba(0,0,0,.45);
    overflow: hidden;
  }
  .card--front { left: 540px; top: 110px; }
  .card--back  { left: 60px;  top: 600px; }

  /* front */
  .holder { position: absolute; left: 44px; top: 40px; width: 260px; }
  .holder__name { color: var(--bronze); font-weight: 700; font-size: 26px; letter-spacing: .3px; }
  .holder__role { color: var(--text-grey); font-size: 14px; margin-top: 2px; }
  .holder__rule { width: 40px; height: 1px; background: var(--bronze-soft); margin: 22px 0 24px; }
  .contact { list-style: none; color: var(--text-grey); font-size: 14.5px; line-height: 1.55; }
  .contact__item { display: flex; align-items: center; gap: 10px; white-space: nowrap; }
  .contact__icon { width: 12px; height: 12px; flex: none; }

  .brand { position: absolute; text-align: center; color: var(--bronze); }
  .brand__name { font-weight: 600; letter-spacing: 1px; line-height: 1; }
  .brand__place { color: var(--text-dim); font-size: 9px; letter-spacing: 3px; text-transform: uppercase; margin-top: 8px; }
  .card--front .brand { right: 40px; top: 96px; }
  .card--front .brand__name { font-size: 52px; }

  .figures {
    position: absolute; left: 300px; bottom: 0; width: 200px; height: 150px;
    background: linear-gradient(180deg, #a8805f 0%, #8f6b4f 100%);
    border-radius: 60px 60px 0 0; opacity: .9;
  }

  /* back */
  .wave-texture {
    position: absolute; inset: 0;
    background: radial-gradient(ellipse at 50% 40%, #2a2829 0%, #1d1c1d 75%);
  }
  .card--back .brand { left: 0; right: 0; top: 78px; }
  .card--back .brand__name { font-size: 64px; }
  .social { position: absolute; left: 0; right: 0; top: 200px; display: flex; justify-content: center; gap: 22px; }
  .social__item { display: flex; align-items: center; gap: 7px; color: var(--text-grey); font-size: 12px; }
  .social__dot { width: 14px; height: 14px; border: 1.2px solid var(--text-grey); border-radius: 50%; }
  .follow { position: absolute; left: 0; right: 0; top: 240px; text-align: center; color: var(--text-grey); font-size: 15px; line-height: 1.5; }
</style>
</head>
<body>
<main class="canvas">

  <section class="card card--front" aria-label="Card front">
    <div class="holder">
      <p class="holder__name">Maren Solvay</p>
      <p class="holder__role">Fashion Marketing</p>
      <div class="holder__rule"></div>
      <ul class="contact">
        <li class="contact__item">4720 N.Alder Crest Ave</li>
        <li class="contact__item">Cedar Vale , CA 90477</li>
        <li class="contact__item">
          <svg class="contact__icon" viewBox="0 0 12 12"><path d="M3 1 L4.6 3.4 L3.6 4.6 Q4.8 7.2 7.4 8.4 L8.6 7.4 L11 9 L10 11 Q3 10.5 1 2 Z" fill="var(--bronze)"/></svg>
          555 010 4821
        </li>
        <li class="contact__item">
          <svg class="contact__icon" viewBox="0 0 12 12" fill="none" stroke="var(--bronze)" stroke-width="1"><circle cx="6" cy="6" r="5"/><ellipse cx="6" cy="6" rx="2.2" ry="5"/><path d="M1 6 H11"/></svg>
          www.lashverastudio.example
        </li>
      </ul>
    </div>
    <div class="brand">
      <p class="brand__name">Lashvera</p>
      <p class="brand__place">Cedar Vale</p>
    </div>
    <div class="figures" role="img" aria-label="Bronze silhouettes of two standing models"></div>
  </section>

  <section class="card card--back" aria-label="Card back">
    <div class="wave-texture" role="img" aria-label="Fine dark wavy line texture"></div>
    <div class="brand">
      <p class="brand__name">Lashvera</p>
      <p class="brand__place">Cedar Vale</p>
    </div>
    <div class="social">
      <span class="social__item"><span class="social__dot"></span>Circlebook</span>
      <span class="social__item"><span class="social__dot"></span>Snapgrid</span>
    </div>
    <p class="follow">Follow Us For Seasonal Campaign News<br>@lashverastudiolounge</p>
  </section>

</main>
</body>
</html>
```